Motor Oil Lubricant Package Labels

We are looking for a logo and label that we can put on our motor oil bottle 1 liter and 5 liter. The name of our motor oil is Corvana. We want to design our flagship logo for CORVANA MOTOR OILS and as well as the label that will go on the bottle. We have some drafts that we have come up with attached and would like to see more options. The concept of a timeless motor oil and the endless loop of lubricating oils incorporated in the design. We will have full synthetic motor oil, a synthetic blend motor, ATF III transmission fluid, KRL-VI transmission fluid. hydraulic oils etc. Examples will be attached
Target Market(s)
Automotive Lubricants and Chemicals
Industry/Entity Type
Automotive
Logo Text
Corvana Lubricants
Font styles to use
Other font styles liked:
- Let designer choose
Requirements
Must have
- The Corvana sign incorporated in a very cool way to our name. Our brand needs to stick out
Nice to have
- Automotive lubricant related and colors red, white, and blue incorporated in the design
Should not have
- Images of individuals and or topics not related to automotive lubricants.

```html
<!DOCTYPE html>
<html lang="en">
<head>
<meta charset="utf-8">
<title>Corvana Motor Oil Labels</title>
<link rel="stylesheet" href="https://fonts.googleapis.com/css2?family=Oswald:wght@500;700&family=Poppins:wght@800&family=Roboto:wght@500&display=swap">
<style>
  :root {
    --backdrop-light: #f4f4f4;
    --backdrop-dark: #dcdcdc;
    --gold-light: #f3df93;
    --gold-mid: #d9b553;
    --gold-dark: #b48a2a;
    --blue-deep: #1e3c9a;
    --blue-light: #3a5cc0;
    --red: #ea1c24;
    --silver-light: #f6f6f6;
    --silver-dark: #9a9a9a;
    --ink: #161616;
    --white: #ffffff;
  }
  html, body {
    margin: 0;
    padding: 0;
    overflow: hidden;
  }
  .canvas {
    position: relative;
    width: 1200px;
    height: 935px;
    overflow: hidden;
    background: radial-gradient(ellipse at 50% 45%, var(--backdrop-light), var(--backdrop-dark));
  }
  .label {
    position: absolute;
    top: 116px;
    width: 433px;
    height: 702px;
    border-radius: 28px;
    overflow: hidden;
    box-shadow: 0 0 0 1px rgba(0,0,0,0.18);
  }
  .label--front { left: 141px; }
  .label--back { left: 625px; }
  .label__art {
    position: absolute;
    inset: 0;
    width: 100%;
    height: 100%;
  }
  .brand-name {
    position: absolute;
    transform: translateX(-50%);
    margin: 0;
    font-family: "Poppins", sans-serif;
    font-weight: 800;
    font-size: 60px;
    line-height: 1;
    color: var(--ink);
    white-space: nowrap;
  }
  .label--front .brand-name { left: 195px; top: 154px; }
  .label--back .brand-name { left: 211px; top: 126px; }
  .grade-text {
    font-family: "Oswald", sans-serif;
    font-weight: 700;
    fill: var(--white);
  }
  .blend-text {
    font-family: "Oswald", sans-serif;
    font-weight: 500;
    fill: var(--white);
    letter-spacing: 2px;
  }
  .seal-text {
    font-family: "Oswald", sans-serif;
    font-weight: 700;
    font-size: 12px;
    fill: var(--ink);
  }
  .volume {
    position: absolute;
    left: 41px;
    top: 652px;
    margin: 0;
    font-family: "Oswald", sans-serif;
    font-weight: 700;
    font-size: 21px;
    color: var(--ink);
  }
  .origin-note {
    position: absolute;
    left: 261px;
    top: 654px;
    margin: 0;
    font-family: "Oswald", sans-serif;
    font-weight: 700;
    font-size: 17px;
    color: var(--white);
  }
  .flag-badge {
    position: absolute;
    left: 48px;
    top: 547px;
    width: 92px;
  }
  .flag-badge__flag {
    height: 48px;
    background: repeating-linear-gradient(to bottom, #c8202f 0 4px, #ffffff 4px 7px);
    position: relative;
  }
  .flag-badge__flag::before {
    content: "";
    position: absolute;
    left: 0;
    top: 0;
    width: 38px;
    height: 26px;
    background: #243c7c;
  }
  .flag-badge__caption {
    margin: 0;
    background: var(--white);
    font-family: "Roboto", sans-serif;
    font-weight: 500;
    font-size: 11.5px;
    text-align: center;
    color: var(--ink);
    padding: 1px 0;
    letter-spacing: 0.5px;
  }
</style>
</head>
<body>
<div class="canvas">

  <!-- Front label -->
  <section class="label label--front">
    <svg class="label__art" viewBox="0 0 433 702" xmlns="http://www.w3.org/2000/svg">
      <defs>
        <linearGradient id="goldFront" x1="0" y1="0" x2="1" y2="0.2">
          <stop offset="0" stop-color="var(--gold-dark)"/>
          <stop offset="0.35" stop-color="var(--gold-light)"/>
          <stop offset="0.6" stop-color="var(--gold-mid)"/>
          <stop offset="1" stop-color="var(--gold-light)"/>
        </linearGradient>
        <linearGradient id="silverFront" x1="0" y1="0" x2="1" y2="0">
          <stop offset="0" stop-color="var(--silver-dark)"/>
          <stop offset="0.5" stop-color="var(--silver-light)"/>
          <stop offset="1" stop-color="var(--silver-dark)"/>
        </linearGradient>
        <radialGradient id="sealGold" cx="0.4" cy="0.35" r="0.7">
          <stop offset="0" stop-color="var(--gold-light)"/>
          <stop offset="1" stop-color="var(--gold-dark)"/>
        </radialGradient>
      </defs>
      <rect class="label__gold" width="433" height="702" fill="url(#goldFront)"/>
      <path class="label__blue-band" d="M95 0 L245 0 Q60 90 0 255 L0 150 Q30 50 95 0 Z" fill="var(--blue-deep)"/>
      <path class="label__blue-stripe" d="M160 0 L205 0 Q50 85 0 215 L0 190 Q45 70 160 0 Z" fill="var(--blue-light)"/>
      <path class="label__silver-arc" d="M433 170 Q212 238 180 702 L201 702 Q232 252 433 182 Z" fill="url(#silverFront)"/>
      <path class="label__red-panel" d="M433 182 Q232 252 201 702 L433 702 Z" fill="var(--red)"/>

      <g class="seal">
        <circle cx="97" cy="394" r="55" fill="url(#sealGold)"/>
        <circle cx="97" cy="394" r="44" fill="none" stroke="var(--gold-dark)" stroke-width="2"/>
        <circle cx="97" cy="394" r="39" fill="var(--white)"/>
        <text class="seal-text" x="97" y="381" text-anchor="middle">FOR</text>
        <text class="seal-text" x="97" y="397" text-anchor="middle">GASOLINE</text>
        <text class="seal-text" x="97" y="413" text-anchor="middle">ENGIENS</text>
      </g>

      <text class="blend-text" font-size="26" transform="translate(283 372) rotate(90)" textLength="204" lengthAdjust="spacingAndGlyphs">SYNTHETIC BLEND</text>
      <text class="grade-text" transform="translate(312 332) rotate(90)" textLength="288" lengthAdjust="spacingAndGlyphs"><tspan font-size="40">SAE</tspan><tspan font-size="80" dx="4">5W-30</tspan><tspan font-size="40" dx="6">APISN</tspan></text>
    </svg>
    <h2 class="brand-name">Corvana</h2>
    <p class="volume">32oz 1946 mU</p>
    <p class="origin-note">Made In USA</p>
  </section>

  <!-- Back label -->
  <section class="label label--back">
    <svg class="label__art" viewBox="0 0 433 702" xmlns="http://www.w3.org/2000/svg">
      <defs>
        <linearGradient id="goldBack" x1="0" y1="0" x2="1" y2="0.2">
          <stop offset="0" stop-color="var(--gold-dark)"/>
          <stop offset="0.35" stop-color="var(--gold-light)"/>
          <stop offset="0.6" stop-color="var(--gold-mid)"/>
          <stop offset="1" stop-color="var(--gold-light)"/>
        </linearGradient>
        <linearGradient id="silverBack" x1="0" y1="0" x2="1" y2="0">
          <stop offset="0" stop-color="var(--silver-dark)"/>
          <stop offset="0.5" stop-color="var(--silver-light)"/>
          <stop offset="1" stop-color="var(--silver-dark)"/>
        </linearGradient>
      </defs>
      <rect class="label__gold" width="433" height="702" fill="url(#goldBack)"/>
      <path class="label__blue-band" d="M95 0 L245 0 Q60 90 0 255 L0 150 Q30 50 95 0 Z" fill="var(--blue-deep)"/>
      <path class="label__blue-stripe" d="M160 0 L205 0 Q50 85 0 215 L0 190 Q45 70 160 0 Z" fill="var(--blue-light)"/>
      <path class="label__silver-arc" d="M433 174 Q215 240 184 702 L205 702 Q236 254 433 186 Z" fill="url(#silverBack)"/>
      <path class="label__red-panel" d="M433 186 Q236 254 205 702 L433 702 Z" fill="var(--red)"/>

      <text class="blend-text" font-size="24" transform="translate(316 364) rotate(90)" textLength="184" lengthAdjust="spacingAndGlyphs">SYNTHETIC BLEND</text>
      <text class="grade-text" transform="translate(343 328) rotate(90)" textLength="260" lengthAdjust="spacingAndGlyphs"><tspan font-size="36">SAE</tspan><tspan font-size="72" dx="4">5W-30</tspan><tspan font-size="36" dx="6">APISN</tspan></text>
    </svg>
    <h2 class="brand-name">Corvana</h2>
    <div class="flag-badge">
      <div class="flag-badge__flag" role="img" aria-label="United States flag"></div>
      <p class="flag-badge__caption">MADE IN USA</p>
    </div>
  </section>

</div>
</body>
</html>
```